VORELT B2B portal design
Fantastic design work, top communication and fast design changes! Many thanks,Jarek & Lutz from VORELT
Zielgruppe
We are a B2B Cloud Services StartUp that creates B2B logistics & supply chain processes between customer and its suppliers.
Aufgabenstellung
We need a modern responsive able design, that should consider that we are NOT presenting goods or clothes or similar on the portal pages but we show mainly data grids, kpi dashboards, forms, and setting panels to our customer and their suppliers.
The design must be clean and straight not to distract people from the important information in these data grids, kpi dashboards, forms, and settings panels.
We need our logo perfectly embedded and the pages coloured around from grey to blue.
The Designer must be able to deliver a design and transfer it to a highly responsive HTML (5) template (without technical content or further functionality). This our programmers will implement afterwards in .Net.
We need in total 3 page templates:
1. Login Page
2. Main Page with overview over the following services text (each one shown in one tile)
"ZMS (Time Frame Management)"
"DMS (Document Management)"
"REMS (Reporting Management)"
-> Note: At the end we will have up to 12 or more tiles (services) so the design should be additive
3. Data grid (e.g. list of customers)/form (e.g. customer registration form) page to show some data grid with database data
See samples for each page enclosed!!

```html
<!DOCTYPE html>
<html lang="en">
<head>
<meta charset="utf-8">
<title>VORELT – Services</title>
<link href="https://fonts.googleapis.com/css2?family=Open+Sans:wght@400;600;700&family=Ubuntu+Condensed&display=swap" rel="stylesheet">
<style>
  :root{
    --navy:#022b47;
    --sidebar:#e2e6e9;
    --sidebar-line:#c9d0d5;
    --page:#f6f8f9;
    --white:#ffffff;
    --text:#1c2b36;
    --green:#5cb85c;
    --green-text:#3f9a3f;
    --blue:#4aaed0;
    --blue-text:#2a88aa;
    --orange:#f0ad4e;
    --orange-text:#d5861b;
    --tile-border:#d9dde0;
  }
  *{box-sizing:border-box;margin:0;padding:0}
  html,body{width:1200px;height:1019px;overflow:hidden;background:var(--page)}
  body{position:relative;font-family:"Open Sans",sans-serif;color:var(--text)}

  .topbar{position:absolute;left:0;top:0;width:1200px;height:72px;background:var(--navy);color:var(--white)}
  .user{position:absolute;right:30px;top:10px;display:flex;align-items:center;gap:14px}
  .user-text{text-align:right}
  .user-name{font-weight:700;font-size:19px;line-height:24px}
  .user-mail{font-size:13px;line-height:18px}
  .avatar{width:52px;height:52px;border-radius:50%;background:radial-gradient(circle at 50% 40%,#9a8f86,#4b4642);border:2px solid #c7ccd0}
  .caret{width:0;height:0;border-left:5px solid transparent;border-right:5px solid transparent;border-top:7px solid var(--white)}

  .sidebar{position:absolute;left:0;top:73px;width:329px;height:885px;background:var(--sidebar)}
  .brand{height:219px;display:flex;align-items:center;justify-content:center;background:linear-gradient(135deg,#d3d8dc 0%,#eceff1 45%,#dde2e5 70%,#eef0f2 100%);border-bottom:1px solid var(--sidebar-line)}
  .brand-name{font-family:"Open Sans",sans-serif;font-weight:700;font-size:54px;letter-spacing:2px;color:var(--navy)}
  .menu{list-style:none}
  .menu-item{height:61px;display:flex;align-items:center;padding-left:20px;gap:12px;border-bottom:1px solid var(--sidebar-line);font-family:"Ubuntu Condensed",sans-serif;font-size:20px;color:var(--text);position:relative}
  .menu-item svg{width:26px;height:26px;flex:none}
  .menu-item.is-active{background:var(--navy);color:var(--white)}
  .chevron{position:absolute;right:18px;top:50%;width:9px;height:9px;border-right:2px solid var(--white);border-top:2px solid var(--white);transform:translateY(-50%) rotate(45deg)}

  .services{position:absolute;left:358px;top:157px;display:flex;gap:12px}
  .tile{width:264px;height:220px;background:var(--white);border:1px solid var(--tile-border);border-radius:3px;overflow:hidden;text-align:center}
  .tile-art{height:157px;display:flex;align-items:center;justify-content:center;position:relative;overflow:hidden}
  .tile-art::after{content:"";position:absolute;inset:0;background:linear-gradient(155deg,rgba(255,255,255,0) 45%,rgba(255,255,255,.07) 45%)}
  .tile-art svg{width:116px;height:116px;position:relative;z-index:1}
  .tile--zms .tile-art{background:var(--green)}
  .tile--dms .tile-art{background:var(--blue)}
  .tile--rems .tile-art{background:var(--orange)}
  .tile-title{font-weight:600;font-size:21px;line-height:26px;margin-top:8px}
  .tile-sub{font-size:15px;line-height:20px}
  .tile--zms .tile-title,.tile--zms .tile-sub{color:var(--green-text)}
  .tile--dms .tile-title,.tile--dms .tile-sub{color:var(--blue-text)}
  .tile--rems .tile-title,.tile--rems .tile-sub{color:var(--orange-text)}

  .footer{position:absolute;left:0;top:958px;width:1200px;height:61px;background:var(--white);border-top:1px solid #e3e6e8;display:flex;align-items:center;justify-content:space-between;padding:0 20px 0 15px;font-family:"Ubuntu Condensed",sans-serif;font-size:16px;color:var(--text)}
</style>
</head>
<body>
  <header class="topbar">
    <div class="user">
      <div class="user-text">
        <div class="user-name">Mark Deller</div>
        <div class="user-mail">mark_deller@postvale.com</div>
      </div>
      <div class="avatar" role="img" aria-label="User profile photo"></div>
      <div class="caret"></div>
    </div>
  </header>

  <nav class="sidebar">
    <div class="brand"><span class="brand-name">VORELT</span></div>
    <ul class="menu">
      <li class="menu-item">
        <svg viewBox="0 0 26 26"><circle cx="13" cy="13" r="10" fill="none" stroke="#022b47" stroke-width="1.6"/><rect x="1" y="10" width="24" height="7" fill="#e2e6e9"/><text x="13" y="16" font-size="7" font-family="Open Sans,sans-serif" font-weight="700" text-anchor="middle" fill="#022b47">NEWS</text></svg>
        My News</li>
      <li class="menu-item">
        <svg viewBox="0 0 26 26" fill="#022b47"><circle cx="10" cy="7" r="5"/><path d="M1 23c0-6 4-10 9-10 3 0 5 1 6 2v8z"/><circle cx="20" cy="19" r="3.5" fill="none" stroke="#022b47" stroke-width="2.2"/></svg>
        My User Settings</li>
      <li class="menu-item">
        <svg viewBox="0 0 26 26" fill="none" stroke="#022b47"><circle cx="9" cy="9" r="4.5" stroke-width="4" stroke-dasharray="2.5 1.6"/><circle cx="19" cy="18" r="3.5" stroke-width="3.4" stroke-dasharray="2 1.4"/></svg>
        Company Settings</li>
      <li class="menu-item">
        <svg viewBox="0 0 26 26" fill="none" stroke="#022b47" stroke-width="2.6" stroke-linecap="round"><path d="M4 22l10-10"/><path d="M15 4a5 5 0 0 0 6 7"/><path d="M6 4l16 16"/></svg>
        Configuration</li>
      <li class="menu-item is-active">
        <svg viewBox="0 0 26 26" fill="#ffffff"><rect x="2" y="4" width="5" height="4"/><rect x="9" y="4" width="15" height="4"/><rect x="2" y="11" width="5" height="4"/><rect x="9" y="11" width="15" height="4"/><rect x="2" y="18" width="5" height="4"/><rect x="9" y="18" width="15" height="4"/></svg>
        Services<span class="chevron"></span></li>
      <li class="menu-item">
        <svg viewBox="0 0 26 26" fill="#022b47"><ellipse cx="14" cy="11" rx="10" ry="7"/><path d="M5 15l-3 6 8-3z"/></svg>
        Communication</li>
      <li class="menu-item">
        <svg viewBox="0 0 26 26" fill="none" stroke="#022b47" stroke-width="2.4"><path d="M11 6H5v15h15v-6"/><path d="M14 4h8v8M22 4L11 15"/></svg>
        Logout</li>
    </ul>
  </nav>

  <main class="services">
    <article class="tile tile--zms">
      <div class="tile-art">
        <svg viewBox="0 0 116 116" fill="none" stroke="#fff" stroke-width="6" stroke-linecap="round"><path d="M58 12a46 46 0 1 1-40 69"/><path d="M30 98l-12-17 20-3"/><path d="M26 30a46 46 0 0 1 8-9" stroke-dasharray="2 10"/><text x="58" y="71" font-size="32" font-family="Open Sans,sans-serif" fill="#fff" stroke="none" text-anchor="middle">24</text></svg>
      </div>
      <div class="tile-title">ZMS</div>
      <div class="tile-sub">Time Frame Management System</div>
    </article>
    <article class="tile tile--dms">
      <div class="tile-art">
        <svg viewBox="0 0 116 116" fill="none" stroke="#fff" stroke-width="4.5" stroke-linejoin="round"><rect x="6" y="62" width="104" height="48"/><path d="M6 62l14-34h76l14 34"/><rect x="30" y="8" width="52" height="24"/><path d="M26 20h60v38H26z" fill="#4aaed0"/><path d="M22 34h70v28H22z" fill="#4aaed0"/><path d="M40 48h30"/><circle cx="58" cy="84" r="6"/></svg>
      </div>
      <div class="tile-title">DMS</div>
      <div class="tile-sub">Document Management System</div>
    </article>
    <article class="tile tile--rems">
      <div class="tile-art">
        <svg viewBox="0 0 116 116" fill="none" stroke="#fff" stroke-width="4.5" stroke-linejoin="round"><path d="M40 6h50v92H28V18"/><rect x="18" y="12" width="62" height="94" fill="#f0ad4e"/><path d="M30 28h38M30 40h38"/><path d="M30 78l12-14 12 10 14-20"/><circle cx="30" cy="78" r="3.5" fill="#fff"/><circle cx="42" cy="64" r="3.5" fill="#fff"/><circle cx="54" cy="74" r="3.5" fill="#fff"/><circle cx="68" cy="54" r="3.5" fill="#fff"/></svg>
      </div>
      <div class="tile-title">REMS</div>
      <div class="tile-sub">Reporting Management System</div>
    </article>
  </main>

  <footer class="footer">
    <span>© 2016 VORELT. All rights reserved.</span>
    <span>Help &nbsp;/&nbsp; Disclaimer &nbsp;/&nbsp; Contact</span>
  </footer>
</body>
</html>
```